Online Advice via Video Site requires Cutting Edge Homepage

We need a creative new and exciting webdesign for our tutoring via video-chat website.

We have prepared a "demo" homepage for you to see various promotional material that we think would be suitable for the homepage. http://www.quillmarsh.com/demo

The actual site is undergoing some final tinkering but can be accessed and used at http://www.quillmarsh.com

There is NO NEED to take any colours or design structure from this.

We expect the logo to be changed to match the new site. The new logo should match the site's function.

I have included some other projects that we like the look of:
http://www.vantoplex.com.au/design/143762
http://www.vantoplex.com.au/design/561630
http://www.vantoplex.com.au/design/247199
http://www.vantoplex.com.au/design/255195
http://www.birchlume.tv/

Target Market(s)

People that will work as tutors/advisers or be student/clients

Industry/Entity Type

Tutoring

Requirements
Must have
• The search is the main feature of the homepage

After the search the next goal of the page is to get people to sign up to the site

Login, (optional inclusion of the gablenet login - if you don't include it then you need only have a "login" button... no username or password input fields)

Footer
Nice to have
• The promotional material for the site, the colours on the Prezi file CAN BE changed to suit the new design you propose.

```html
<!DOCTYPE html>
<html lang="en">
<head>
<meta charset="utf-8">
<title>Quill Marsh – advice when it suits you</title>
<link rel="stylesheet" href="https://fonts.googleapis.com/css2?family=Arimo:wght@400;700&family=Shadows+Into+Light&family=Sacramento&display=swap">
<style>
  :root {
    --page: #fbf8d0;
    --ink: #2d2a28;
    --muted: #5a5650;
    --magenta: #c50a48;
    --magenta-deep: #a50a3b;
    --magenta-bright: #dc0f55;
    --berry: #a6083f;
    --mustard: #dfc818;
    --panel: #ffffff;
    --field: #ffffff;
    --social: #6b6b6b;
  }
  * { box-sizing: border-box; margin: 0; padding: 0; }
  html, body { width: 1093px; height: 1200px; overflow: hidden; }
  body {
    position: relative;
    background: var(--page);
    font-family: "Arimo", Arial, sans-serif;
    color: var(--ink);
  }
  .abs { position: absolute; }
  .hand { font-family: "Shadows Into Light", cursive; }

  /* header */
  .brand {
    left: 29px; top: 16px; line-height: 1;
    font-size: 38px; color: var(--ink); letter-spacing: 1px;
    display: flex; align-items: center; gap: 8px; white-space: nowrap;
  }
  .brand-dot { width: 12px; height: 12px; border-radius: 50%; background: var(--berry); }
  .login-label { right: 514px; top: 31px; font-size: 12.5px; white-space: nowrap; line-height: 14px; }
  .login-field { top: 25px; width: 159px; height: 26px; background: var(--field); }
  .field-user { left: 588px; }
  .field-pass { left: 751px; }
  .login-note { top: 57px; font-size: 11px; white-space: nowrap; }
  .note-remember { left: 658px; }
  .note-forgot { left: 774px; }
  .sign-in {
    left: 917px; top: 26px; width: 63px; height: 25px;
    background: var(--berry); color: #fff; border-radius: 4px;
    font-size: 12px; font-weight: 700; display: flex; align-items: center; justify-content: center;
  }
  .join { left: 990px; top: 24px; font-size: 23px; line-height: 1.2; color: var(--ink); white-space: nowrap; }
  .social { left: 940px; top: 74px; display: flex; gap: 2px; }
  .social span { width: 26px; height: 26px; border-radius: 50%; background: var(--social); display: block; }
  .tagline { left: 17px; top: 97px; font-size: 13px; line-height: 16px; color: var(--ink); white-space: nowrap; }

  /* hero search */
  .hero {
    left: 11px; top: 126px; width: 1070px; height: 255px;
    background: radial-gradient(ellipse at 50% 20%, var(--magenta-bright) 0%, var(--magenta) 55%, var(--magenta-deep) 100%);
  }
  .search-field {
    left: 42px; top: 63px; width: 704px; height: 77px;
    background: linear-gradient(#fbfbfb, #ececec);
    border-radius: 4px 0 0 4px;
    font-size: 22px; line-height: 77px; color: #6c6c6c; padding-left: 26px;
  }
  .search-btn {
    left: 746px; top: 63px; width: 245px; height: 77px; background: var(--mustard);
    display: flex; align-items: center; padding-left: 38px; gap: 28px;
    font-size: 25px; color: #fff; white-space: nowrap;
  }
  .hero-point {
    font-size: 14.5px; line-height: 18px; color: #fff; white-space: nowrap;
    display: flex; align-items: center; gap: 7px;
  }
  .hero-point svg { flex: none; }

  /* advisors */
  .panel { background: var(--panel); box-shadow: 0 1px 4px rgba(0,0,0,.08); }
  .advisors { left: 13px; top: 403px; width: 1068px; height: 371px; }
  .advisors h2 { position: absolute; left: 58px; top: 74px; font-weight: 400; font-size: 21px; line-height: 26px; }
  .perk { font-size: 12.5px; line-height: 16px; white-space: nowrap; }
  .video-frame { left: 634px; top: 31px; width: 394px; height: 278px; background: #fff; box-shadow: 0 0 6px rgba(0,0,0,.12); }
  .video-still {
    left: 8px; top: 10px; width: 377px; height: 261px;
    background: linear-gradient(180deg, #bcd0dc 0%, #9fb4a8 38%, #5f8a35 62%, #3f6b1c 100%);
  }
  .play { left: 166px; top: 112px; }

  /* topics */
  .topics { left: 13px; top: 798px; width: 1068px; height: 280px; }
  .topic-art { position: absolute; top: 30px; width: 200px; height: 140px; }
  .art-math { left: 49px; background: linear-gradient(135deg, #f2efe8, #e7c98c 50%, #dcd7cc); }
  .art-lang { left: 325px; background: linear-gradient(90deg, #f4a79b, #bfe0a5 35%, #b3d5ef 65%, #f2f1ea); }
  .art-eng { left: 622px; background: linear-gradient(135deg, #f09aa8, #d98ae0 45%, #9bcff0 80%, #f7f5f5); }
  .art-tech { left: 842px; background: linear-gradient(90deg, #c5d8ee, #5f90d0 55%, #e7eef6); }
  .topic-name {
    position: absolute; top: 196px; transform: translateX(-50%); line-height: 40px;
    font-family: "Sacramento", cursive; font-size: 35px; color: var(--berry); white-space: nowrap;
  }

  /* footer */
  .footer-links { left: 0; width: 1093px; top: 1104px; text-align: center; font-size: 11.5px; color: var(--muted); }
  .credit { left: 0; width: 1093px; top: 1132px; text-align: center; font-size: 11px; color: var(--muted); }
</style>
</head>
<body>
  <header>
    <div class="abs brand hand"><span>quill marsh</span><span class="brand-dot"></span></div>
    <div class="abs login-label">GABLENET LOGIN</div>
    <div class="abs login-field field-user"></div>
    <div class="abs login-field field-pass"></div>
    <div class="abs sign-in">sign in</div>
    <div class="abs join hand">join here</div>
    <div class="abs login-note note-remember">remember me</div>
    <div class="abs login-note note-forgot">forgot password</div>
    <div class="abs social" aria-label="social links"><span></span><span></span><span></span><span></span></div>
    <p class="abs tagline hand">Imagine if, whenever you had a problem you could instantly access the world's experts to solve it. Now you can!*</p>
  </header>

  <section class="abs hero">
    <div class="abs search-field">search for topics and advisors</div>
    <div class="abs search-btn hand">
      <span>search here</span>
      <svg width="56" height="56" viewBox="0 0 56 56" aria-hidden="true">
        <circle cx="22" cy="22" r="15" fill="none" stroke="#fff" stroke-width="7"/>
        <line x1="33" y1="33" x2="51" y2="51" stroke="#fff" stroke-width="9" stroke-linecap="round"/>
      </svg>
    </div>
    <div class="abs hero-point hand" style="left:44px;top:172px"><svg width="9" height="12" viewBox="0 0 9 12"><path d="M1 1l6 5-6 5" fill="none" stroke="#fff" stroke-width="2.4"/></svg>Quillmarsh is the place for e-learning, mentoring &amp; professional advice</div>
    <div class="abs hero-point hand" style="left:44px;top:204px"><svg width="9" height="12" viewBox="0 0 9 12"><path d="M1 1l6 5-6 5" fill="none" stroke="#fff" stroke-width="2.4"/></svg>It instantly connects people with knowledge and those who need it</div>
    <div class="abs hero-point hand" style="left:613px;top:172px"><svg width="9" height="12" viewBox="0 0 9 12"><path d="M1 1l6 5-6 5" fill="none" stroke="#fff" stroke-width="2.4"/></svg>Connects people for ongoing advice or on off answers</div>
    <div class="abs hero-point hand" style="left:613px;top:204px"><svg width="9" height="12" viewBox="0 0 9 12"><path d="M1 1l6 5-6 5" fill="none" stroke="#fff" stroke-width="2.4"/></svg>Ask questions and/or work exactly when it suits you</div>
  </section>

  <section class="abs panel advisors">
    <h2>advisors</h2>
    <p class="abs perk" style="left:58px;top:115px">• Teach the topics you know well</p>
    <p class="abs perk" style="left:58px;top:147px">• Educate people in your spare time</p>
    <p class="abs perk" style="left:58px;top:179px">• Answer single questions</p>
    <p class="abs perk" style="left:58px;top:211px">• Provide ongoing tutoring</p>
    <p class="abs perk" style="left:324px;top:112px">• Work when it suits you</p>
    <p class="abs perk" style="left:324px;top:137px">• Pre-book appointments</p>
    <p class="abs perk" style="left:324px;top:163px">• Answer questions only when you can</p>
    <p class="abs perk" style="left:324px;top:188px">• Earn money for your time</p>
    <p class="abs perk" style="left:324px;top:214px">• Set your own fee rate</p>
    <div class="abs video-frame">
      <div class="abs video-still" role="img" aria-label="Video still: a person in a field of tall grass looking through binoculars">
        <svg class="abs play" width="68" height="68" viewBox="0 0 68 68" aria-hidden="true">
          <circle cx="34" cy="34" r="31" fill="none" stroke="#fff" stroke-width="4"/>
          <path d="M26 19l22 15-22 15z" fill="#fff"/>
        </svg>
      </div>
    </div>
  </section>

  <section class="abs panel topics">
    <div class="topic-art art-math" role="img" aria-label="Wooden toy blocks spelling math beside an abacus toy"></div>
    <div class="topic-art art-lang" role="img" aria-label="Hanging speech-bubble tags saying hello in many languages"></div>
    <div class="topic-art art-eng" role="img" aria-label="Colourful 3D alphabet letters"></div>
    <div class="topic-art art-tech" role="img" aria-label="Row of computer screens in perspective"></div>
    <span class="topic-name" style="left:149px">Mathematics</span>
    <span class="topic-name" style="left:425px">Languages</span>
    <span class="topic-name" style="left:722px">English</span>
    <span class="topic-name" style="left:942px">Technology</span>
  </section>

  <footer>
    <nav class="abs footer-links">Home | Student | Advisors | Topics | Blog | FAQs | Sitemap | About us | Our Technology | Contact</nav>
    <p class="abs credit">Web Designed &amp; Development By Tarnwell Studio</p>
  </footer>
</body>
</html>
```